Probate (Legal) Wordpress Design with Coding for Online Company

I need a Wordpress design with coding, pictures, content to be provided by me, fully responsive, and development. This is for a 6-7 page design.

Pages Needed: Home/About/Probate/Process/FAQ/Contact Us/Blog.

The home page should be organized as followed:
-Steps in Probate: Gather; Implement; Close (each step will come with content)
-Flat-Fee Price & Savings: Content will go here with a button to contact us (phone number) or just the phone number.
-You Have Questions, We Have Answers: five questions with content. Only one question answer to show at a time when clicked on the question from the list.
-Get to Know Us: a brief description with content about what we do and who we are.

Main image slogan: Helping Californians deal with loss with DIGNITY & UNDERSTATING (you may use a better slogan if you wish).

The Contact page should not have a map since we are an online company. We service the entire state of California in every county and city.

The About page should be simple, direct, and easy on the eye. It should have a brief description of who we are and it should have no more than 6 reasons why the client should hire us.

About our online California company. We are not attorneys but legal document assistants who prepare legal documents for probate estate when someone dies with or without a will and assets need to be distributed. We have a flat-fee for Formal Probate of $999 and $699 for Informal Probate. We are an online company and offer our services to the entire state of California in every county. We do everything over the phone and email. The turn around time for us to prepare the initial legal paperwork for the client is within 3-5 business days. We can prepare, file, serve and manage a probate matter from petition to closing. We are not attorneys so our prices are very affordable compare to the attorney.

The company name for the website will be www.velmarhollow.com, The Velmar Hollow Group.

I do not have a logo yet. The colors of the website should be easy on the eye and calming. THE SITE SHOULD BE SIMPLE AND STRAIGHT TO THE POINT. EASY TO NAVIGATE.

The company phone number should be very visible and should stand out to the client. It should also be clickable and ready to dial for smartphone users.

I do not want a contact form on the homepage. THE MAIN THING IS FOR THE POTENTIAL CLIENT TO CALL OUR OFFICE TO SIGN UP.

I do like some images of family or people since we are dealing with people who just lost a loved one. Not all the images have to be of people.

The site should not look like we practice law or that people can mistake us for attorneys.

Target Market(s)

People who just lost a loved one who had property, assets, in California but died with or without a will or trust. This is for people looking to hire non-attorneys.

Coding

Coded - Design and coding required

Font styles to use
Serif

Colors

Designer to choose colors to be used in the design.

Requirements
Must have
• Refer to Project Description.
Nice to have
• The sample images provided is what I am attracted to for the homepage image.
Should not have

```html
<!DOCTYPE html>
<html lang="en">
<head>
<meta charset="utf-8">
<title>FAQ – The Velmar Hollow Group</title>
<link rel="stylesheet" href="https://fonts.googleapis.com/css2?family=Crimson+Pro:wght@600;700&family=Open+Sans:wght@400;600;700&display=swap">
<style>
:root{
  --orange:#ff7f00;
  --teal:#17677f;
  --teal-band:#1f86a8;
  --amber-band:#a86a1c;
  --ink:#222;
  --muted:#444;
  --white:#fff;
  --hero-a:#6f6f6f;
  --hero-b:#9a8f86;
}
*{margin:0;padding:0;box-sizing:border-box}
html,body{width:710px;height:1200px;overflow:hidden;background:var(--white)}
body{position:relative;font-family:"Open Sans",Arial,sans-serif;color:var(--ink)}
.serif{font-family:"Crimson Pro",Georgia,serif}

/* header */
.site-header{position:absolute;left:0;top:0;width:710px;height:74px;border-top:2px solid var(--orange);background:var(--white)}
.call-tab{position:absolute;left:468px;top:0;width:174px;height:24px;background:var(--orange);border-radius:0 0 16px 16px;color:var(--white);font-size:10px;font-weight:700;display:flex;align-items:center;justify-content:center;gap:6px}
.brand{position:absolute;left:58px;top:40px;display:flex;align-items:center;gap:6px}
.brand-mark{width:12px;height:12px;background:var(--orange)}
.brand-name{font-family:"Crimson Pro",Georgia,serif;font-weight:700;font-size:13px;color:var(--teal);text-transform:uppercase;letter-spacing:.3px}
.main-nav{position:absolute;left:270px;top:46px;display:flex;gap:22px;font-size:9.5px;font-weight:600;color:var(--ink)}

/* hero */
.page-hero{position:absolute;left:0;top:74px;width:710px;height:114px;background:linear-gradient(90deg,var(--hero-a) 0%,#7a7673 45%,var(--hero-b) 100%)}
.page-hero h1{position:absolute;left:58px;top:38px;font-family:"Crimson Pro",Georgia,serif;font-weight:700;font-size:32px;color:var(--white)}

/* faq */
.faq-title{position:absolute;left:0;width:710px;top:228px;text-align:center;font-family:"Crimson Pro",Georgia,serif;font-weight:700;font-size:19px;color:var(--teal);letter-spacing:.5px}
.faq-rule{position:absolute;left:332px;top:265px;width:46px;height:2px;background:var(--teal)}
.question-active{position:absolute;left:160px;top:305px;width:390px;height:30px;background:var(--orange);border-radius:15px;color:var(--white);font-size:9px;font-weight:600;display:flex;align-items:center;justify-content:center}
.question-pointer{position:absolute;left:342px;top:334px}
.answer-heading{position:absolute;left:0;width:710px;top:375px;text-align:center;font-size:11px;font-weight:700;color:var(--teal);letter-spacing:.3px}
.answer-text{position:absolute;left:60px;width:590px;top:398px;text-align:center;font-size:8.2px;line-height:13.2px;color:var(--muted)}
.answer-points{position:absolute;left:0;width:710px;top:456px;list-style:none;text-align:center;font-size:8.2px;line-height:18.2px;color:var(--ink)}
.question-list{position:absolute;left:160px;top:549px;width:390px;list-style:none}
.question-list li{height:30px;margin-bottom:5.5px;border:2px solid var(--teal);border-radius:15px;color:var(--teal);font-size:9px;font-weight:600;display:flex;align-items:center;justify-content:center}

/* info bands */
.info-band{position:absolute;top:734px;width:355px;height:288px;color:var(--white)}
.info-band.what{left:0;background:linear-gradient(135deg,#2a8fb2,var(--teal-band) 60%,#1a7394)}
.info-band.who{left:355px;background:linear-gradient(135deg,#b8772a,var(--amber-band) 60%,#955d16)}
.info-band h2{position:absolute;left:58px;top:36px;font-family:"Crimson Pro",Georgia,serif;font-weight:700;font-size:19px;letter-spacing:.5px}
.info-band.who h2,.info-band.who .band-rule,.info-band.who p,.info-band.who .read-more{left:19px}
.band-rule{position:absolute;left:58px;top:70px;width:64px;height:1.5px;background:var(--white)}
.info-band p{position:absolute;left:58px;width:282px;font-size:8.2px;line-height:14.4px;font-weight:600}
.info-band p.first{top:94px}
.info-band p.second{top:150px}
.read-more{position:absolute;left:58px;top:212px;width:68px;height:32px;border:2px solid var(--white);font-size:9.5px;font-weight:600;display:flex;align-items:center;justify-content:center}

/* footer */
.footer-nav{position:absolute;left:0;width:710px;top:1063px;display:flex;justify-content:center;gap:15px;font-size:9.5px;font-weight:600;color:var(--ink)}
.footer-nav .sep{color:var(--ink);font-weight:400}
.footer-contact{position:absolute;left:0;width:710px;top:1107px;display:flex;justify-content:center;gap:26px;font-size:12.5px;color:var(--ink)}
.contact-item{display:flex;align-items:center;gap:8px}
.footer-rule{position:absolute;left:58px;top:1155px;width:594px;height:1px;background:var(--ink)}
.copyright{position:absolute;left:0;width:710px;top:1171px;text-align:center;font-size:8.8px;font-weight:600;color:var(--ink)}
</style>
</head>
<body>

<header class="site-header">
  <div class="call-tab">
    <svg width="9" height="9" viewBox="0 0 10 10" aria-hidden="true"><rect x="0" y="0" width="10" height="10" rx="2" fill="#fff"/><path d="M3 2.2l1 1.6-.6.7c.4.9 1 1.5 1.9 1.9l.7-.6 1.6 1-.5 1.2C4.6 7.8 2.4 5.6 2 3z" fill="#ff7f00"/></svg>
    Call Us At: +180 555 0147
  </div>
  <div class="brand">
    <span class="brand-mark"></span>
    <span class="brand-name">The Velmar Hollow Group</span>
  </div>
  <nav class="main-nav">
    <span>HOME</span><span>ABOUT</span><span>PROBATE</span><span>PROCESS</span><span>FAQ</span><span>CONTACT US</span><span>BLOG</span>
  </nav>
</header>

<section class="page-hero" role="img" aria-label="Photo of children embracing a parent">
  <h1>FAQ</h1>
</section>

<h2 class="faq-title">OUR FAQ</h2>
<div class="faq-rule"></div>

<div class="question-active">Nemo enim ipsam voluptatem quia voluptas?</div>
<svg class="question-pointer" width="26" height="16" viewBox="0 0 26 16" aria-hidden="true"><path d="M0 0h26L13 16z" fill="#ff7f00"/></svg>

<h3 class="answer-heading">NEMO ENIM IPSAM VOLUPTATEM:</h3>
<p class="answer-text">Sed ut perspiciatis unde omnis iste natus error sit voluptatem accusantium dolorem que laudantium, totam rem aperiam, eaque ipsa quae ab illo inventore veritatis et quasi architecto beatae vitae dicta sunt explicabo. Nemo enim ipsam voluptatem quia voluptas sit aspernatur aut odit aut fugit, sed quia consequuntur magni dolores eos qui ratione voluptatem sequi nesciunt.</p>
<ul class="answer-points">
  <li>Sed ut perspiciatis unde omnis iste natus error sit voluptate.</li>
  <li>Accusantium dolorem que laudantium, totam rem.</li>
  <li>Aperiam, eaque ipsa quae ab illo inventore veritatis.</li>
  <li>Quasi architecto beatae vitae dicta sunt explicabo.</li>
</ul>

<ul class="question-list">
  <li>Magni dolores eos qui ratione voluptatem?</li>
  <li>Sed ut perspiciatis unde omnis natus?</li>
  <li>Enim ad minima veniam, quis nostrum?</li>
  <li>Quis autem vel eum iure reprehenderit?</li>
</ul>

<section class="info-band what" role="img" aria-label="Tinted photo of hands reviewing paperwork">
  <h2>WHAT WE DO</h2>
  <div class="band-rule"></div>
  <p class="first">Sed ut perspiciatis unde omnis iste natus error sit voluptatem accusantium doloremque laudantium, totam rem aperiam, eaque ipsa quae ab illo inventore veritatis et quasi architecto beatae.</p>
  <p class="second">Nemo enim ipsam voluptatem quia voluptas sit aspernatur aut odit aut fugit, sed quia consequuntur magni dolores eos qui ratione voluptatem.</p>
  <div class="read-more">READ MORE</div>
</section>

<section class="info-band who" role="img" aria-label="Tinted photo of a hand signing a document">
  <h2>WHO WE ARE</h2>
  <div class="band-rule"></div>
  <p class="first">Sed ut perspiciatis unde omnis iste natus error sit voluptatem accusantium doloremque laudantium, totam rem aperiam, eaque ipsa quae ab illo inventore veritatis et quasi architecto beatae.</p>
  <p class="second">Nemo enim ipsam voluptatem quia voluptas sit aspernatur aut odit aut fugit, sed quia consequuntur magni dolores eos qui ratione voluptatem.</p>
  <div class="read-more">READ MORE</div>
</section>

<nav class="footer-nav">
  <span>HOME</span><span class="sep">|</span><span>ABOUT</span><span class="sep">|</span><span>PROBATE</span><span class="sep">|</span><span>PROCESS</span><span class="sep">|</span><span>FAQ</span><span class="sep">|</span><span>CONTACT US</span><span class="sep">|</span><span>BLOG</span>
</nav>

<div class="footer-contact">
  <div class="contact-item">
    <svg width="27" height="27" viewBox="0 0 27 27" aria-hidden="true"><circle cx="13.5" cy="13.5" r="12.5" fill="none" stroke="#222" stroke-width="1.5"/><path d="M10 8l2 3-1 1.2c.7 1.5 1.8 2.6 3.3 3.3l1.2-1 3 2-.9 2C12 18 9 15 8.5 9z" fill="#222"/></svg>
    <span>+180 555 0147</span>
  </div>
  <div class="contact-item">
    <svg width="27" height="27" viewBox="0 0 27 27" aria-hidden="true"><circle cx="13.5" cy="13.5" r="12.5" fill="none" stroke="#222" stroke-width="1.5"/><rect x="8" y="9.5" width="11" height="8" rx="1" fill="none" stroke="#222" stroke-width="1.3"/><path d="M8.3 10l5.2 4 5.2-4" fill="none" stroke="#222" stroke-width="1.3"/></svg>
    <span>info@velmarhollow.com</span>
  </div>
</div>

<div class="footer-rule"></div>
<p class="copyright">Copyrights @ 2017 The Velmar Hollow Group. All Rights Reserved.</p>

</body>
</html>
```